Velorin Wine Label For Canopy Haven

Lantern Brook Winery is in need of a wine label for new wine being release. This wine will be used as a fundraiser for Canopy Haven, a chimpanzee santuary in Georgia. The label should reflect a high-end, classy image and the label should suggest the chimp philanthropy without specifically naming the organization (for legal purposes). The label can be a little whimsical without being too cartoonish or child like. This wine will be sold for $30 so it should project a sense of elegance too.
Updates

holiday season makes it difficult to get feedback necessary for approval. just need a few more days...

Industry/Entity Type

Winery

Font styles to use
Sans Serif

Requirements
Must have
• Label should show common design appearance as other labels downloaded.
• Label should be a dark (emerald) green color. Label should have wine name "Velorin" in center. Label should include an image or silhouette of a chimp on it
Should not have
• no cartoonish images;

```html
<!DOCTYPE html>
<html lang="en">
<head>
<meta charset="utf-8">
<title>Velorin Wine Label</title>
<link href="https://fonts.googleapis.com/css2?family=Cinzel:wght@400;700&display=swap" rel="stylesheet">
<style>
  :root {
    --emerald: #02432e;
    --gold: #c8852c;
    --paper: #ffffff;
    --fur-dark: #3a2a1c;
    --fur-light: #b59a78;
  }
  * { margin: 0; padding: 0; box-sizing: border-box; }
  html, body { width: 1200px; height: 805px; overflow: hidden; background: var(--paper); }
  body { font-family: "Cinzel", serif; color: var(--gold); }
  .label { position: relative; width: 1200px; height: 805px; }
  .label-shape { position: absolute; inset: 0; }

  .emblem {
    position: absolute; left: 125px; top: 157px; width: 126px; height: 126px;
    background: var(--gold); transform: rotate(45deg) scale(0.707);
  }
  .portrait {
    position: absolute; left: 534px; top: 198px; width: 132px; height: 152px;
    border-radius: 48% 48% 42% 42%;
    background: radial-gradient(ellipse at 50% 60%, var(--fur-light) 0%, #7b5f44 45%, var(--fur-dark) 85%);
  }
  .rule { position: absolute; height: 1px; background: var(--gold); opacity: .55; left: 441px; width: 318px; }
  .wine-name {
    position: absolute; left: 0; width: 1200px; top: 378px; text-align: center;
    font-size: 80px; line-height: 86px; letter-spacing: 4px; font-weight: 400;
  }
  .brand {
    position: absolute; left: 0; width: 1200px; top: 512px; text-align: center;
    font-weight: 700; line-height: 1;
  }
  .brand-main { display: block; font-size: 34px; letter-spacing: 2px; }
  .brand-sub { display: block; font-size: 24px; letter-spacing: 3px; margin-top: 4px; }

  .spec { position: absolute; top: 634px; font-size: 13px; font-weight: 700; letter-spacing: .5px; }
  .spec-abv { left: 366px; }
  .spec-volume { left: 727px; }

  .vertical { position: absolute; writing-mode: vertical-rl; transform: rotate(180deg); }
  .cause { left: 157px; top: 305px; height: 345px; font-size: 15px; line-height: 20px; letter-spacing: .4px; }
  .warning-title { left: 926px; top: 250px; height: 235px; font-size: 11px; font-weight: 700; }
  .warning-rule { position: absolute; left: 952px; top: 249px; width: 1px; height: 234px; background: var(--gold); }
  .warning-text { left: 963px; top: 150px; height: 336px; font-size: 10.5px; line-height: 18.4px; letter-spacing: .2px; }

  .producer { position: absolute; left: 893px; width: 210px; top: 531px; text-align: center; font-size: 11.5px; line-height: 18px; }
  .producer strong { font-weight: 700; }
  .website {
    position: absolute; left: 893px; top: 596px; width: 210px; height: 31px;
    border: 1.5px solid var(--gold); text-align: center; line-height: 28px;
    font-size: 11px; font-weight: 700; letter-spacing: .3px;
  }
  .sulfites { position: absolute; left: 893px; width: 210px; top: 638px; text-align: center; font-size: 11.5px; }
</style>
</head>
<body>
<main class="label">
  <svg class="label-shape" width="1200" height="805" viewBox="0 0 1200 805" aria-hidden="true">
    <rect x="69" y="119" width="1062" height="565" fill="var(--emerald)"/>
    <polygon points="600,36 886,402 600,768 314,402" fill="var(--emerald)"/>
    <rect x="85" y="135" width="1030" height="533" fill="none" stroke="var(--gold)" stroke-width="3"/>
    <polygon points="600,63 865,402 600,741 335,402" fill="var(--emerald)" stroke="var(--gold)" stroke-width="9"/>
    <polygon points="600,101 835,402 600,703 365,402" fill="none" stroke="var(--gold)" stroke-width="2"/>
  </svg>

  <div class="emblem" role="img" aria-label="Winery crest: diamond with sun, grapes, mountain and hills"></div>
  <div class="portrait" role="img" aria-label="Engraved illustration of a chimpanzee head"></div>

  <div class="rule" style="top:377px"></div>
  <h1 class="wine-name">VELORIN</h1>
  <div class="rule" style="top:465px"></div>

  <div class="brand"><span class="brand-main">LANTERN</span><span class="brand-sub">BROOK</span></div>

  <p class="spec spec-abv">11.6% ALC/VOL</p>
  <p class="spec spec-volume">750ML</p>

  <p class="vertical cause">This wine will be used as a fundraiser<br>for Canopy Haven, a chimpanzee<br>santuary in Georgia.</p>

  <p class="vertical warning-title">GOVERNMENT WARNING:</p>
  <div class="warning-rule"></div>
  <p class="vertical warning-text">(1)&nbsp;According to the surgeon general, women<br>should not drink alcoholic beverages during<br>pregnancy because of the risk of birt deffects.<br>(2)&nbsp;Consumption of alcoholic beverages impairs<br>your ability to drive a car or operate machinery,<br>and may cause health problems.</p>

  <p class="producer">Produced &amp; bottled at<br><strong>LANTERN BROOK, RESORT<br>&amp; SPA HARLOW SPRINGS GA</strong></p>
  <p class="website">WWW.LANTERNBROOKGA.COM</p>
  <p class="sulfites">Contains Sulfites</p>
</main>
</body>
</html>
```